Corwin Ashby College of Nursing website

Nursing college needs a fresh, streamlined website. Many of the items on our website are required by accreditation organizations.

```html
<!DOCTYPE html>
<html lang="en">
<head>
<meta charset="utf-8">
<title>Corwin Ashby College of Nursing</title>
<link href="https://fonts.googleapis.com/css2?family=Lato:wght@400;700&family=Tinos:wght@400;700&display=swap" rel="stylesheet">
<style>
:root{
  --navy:#0b4a7a;
  --blue:#1566a8;
  --green:#0b6b4f;
  --red:#c8102e;
  --ink:#1c1c1c;
  --text:#444;
  --line:#e3e6ea;
  --dark:#1f1f1f;
}
*{box-sizing:border-box;margin:0;padding:0}
html,body{width:1200px;height:4128px;overflow:hidden;background:#fff}
body{font-family:"Lato",sans-serif;color:var(--text);position:relative}
.serif{font-family:"Tinos",serif}
a{color:inherit;text-decoration:none}
.abs{position:absolute}
.btn{position:absolute;display:flex;align-items:center;justify-content:center;background:var(--green);color:#fff;border-radius:22px;font-size:15px;height:42px;width:148px}

/* header */
.site-header{position:absolute;top:0;left:0;width:1200px;height:77px;background:#fff;z-index:3}
.brand{position:absolute;left:112px;top:14px;display:flex;align-items:center;gap:10px}
.brand-mark{width:48px;height:48px;border-radius:50%;background:var(--navy)}
.brand-name{font-family:"Tinos",serif;color:var(--ink);font-size:20px;line-height:1.05}
.brand-name small{display:block;font-size:13px}
.main-nav{position:absolute;top:22px;left:387px;display:flex;gap:0;font-size:15px;color:#333}
.main-nav a{padding:7px 18px}
.main-nav a.active{background:var(--navy);color:#fff;border-radius:16px}

/* hero */
.hero{position:absolute;top:77px;left:0;width:1200px;height:705px}
.hero-photo{position:absolute;inset:0;background:linear-gradient(180deg,#7e848c 0%,#5b6470 35%,#3a4556 65%,#263556 100%)}
.hero-shade{position:absolute;inset:0;background:rgba(10,20,40,.25)}
.hero h1{position:absolute;top:76px;width:100%;text-align:center;color:#fff;font-size:60px;font-weight:700}
.hero p{position:absolute;top:160px;left:240px;width:720px;text-align:center;color:#fff;font-size:19px;line-height:27px}
.hero .btn{top:243px;left:526px}
.hero-curve{position:absolute;left:0;bottom:0;width:1200px;height:130px}

/* about */
.round-photo{position:absolute;width:458px;height:458px;border-radius:50%}
.arc{position:absolute}
.section-title{position:absolute;font-family:"Tinos",serif;font-weight:700;font-size:41px;color:var(--ink)}
.section-title span{color:var(--navy)}
.copy{position:absolute;font-size:14.5px;line-height:23px;color:#444}
.copy p+p{margin-top:28px}

/* notice */
.notice{position:absolute;left:112px;top:1389px;width:976px;height:492px;border-radius:40px;background:linear-gradient(180deg,#0b4b7c,#0a4270);overflow:hidden}
.notice h2{position:absolute;top:100px;width:100%;text-align:center;font-family:"Tinos",serif;font-size:44px;line-height:49px;color:#fff;font-weight:700}
.notice p{position:absolute;top:218px;left:100px;width:776px;text-align:center;color:#fff;font-size:14.5px;line-height:27px}
.notice .btn{top:350px;left:413px}

/* cards */
.info-card{position:absolute;top:1972px;width:225px;height:261px;border:1px solid var(--line);border-radius:12px;background:#fff;padding:20px 18px}
.info-card .icon{width:58px;height:58px;border:1px solid var(--line);border-radius:8px;display:flex;align-items:center;justify-content:center}
.info-card h3{margin-top:22px;font-size:16.5px;font-weight:400;color:#111;border-left:2px solid var(--green);padding-left:10px;line-height:17px}
.info-card ul{list-style:none;margin-top:20px;font-size:12.5px;line-height:19.5px}
.info-card li.link{color:var(--green)}
.info-card.featured{background:var(--green);border-color:var(--green)}
.info-card.featured h3,.info-card.featured ul{color:#fff;border-color:#fff}
.info-card.featured .icon{background:rgba(255,255,255,.15);border-color:transparent}

/* news */
.news-card{position:absolute;top:2936px;width:312px;height:415px;background:#fff;border-radius:6px;box-shadow:0 2px 10px rgba(0,0,0,.12);text-align:center}
.news-card .thumb{height:204px;border-radius:6px 6px 0 0}
.news-card h3{margin:20px 22px 0;font-family:"Tinos",serif;color:var(--navy);font-size:22px;line-height:30px}
.news-card p{margin:14px 28px 0;font-size:12.5px;line-height:21px;color:#555}
.news-card .go{position:absolute;left:136px;bottom:-20px;width:40px;height:40px;border-radius:50%;background:var(--green);display:flex;align-items:center;justify-content:center}

/* footer */
.site-footer{position:absolute;left:0;top:3525px;width:1200px;height:603px}
.footer-seal{position:absolute;left:525px;top:72px;width:150px;height:150px;border-radius:50%;background:#fff;border:3px solid var(--navy)}
.fcol{position:absolute;top:280px;color:#fff}
.fcol h4{font-size:21px;font-weight:700;margin-bottom:30px}
.fcol ul{list-style:none;font-size:15px;line-height:38.5px}
.contact-row{display:flex;gap:18px;font-size:15px;line-height:25px;margin-bottom:30px;align-items:flex-start}
.social{display:flex;gap:16px;margin-top:26px}
.social span{width:24px;height:24px;border:2px solid #fff;border-radius:50%}
.social span:first-child{background:var(--green);border-color:#fff;width:34px;height:34px;border-radius:6px;margin-top:-5px}
.copyright{position:absolute;top:572px;width:100%;text-align:center;color:#fff;font-size:13px}
</style>
</head>
<body>

<header class="site-header">
  <a class="brand" href="#">
    <span class="brand-mark"></span>
    <span class="brand-name">Corwin Ashby<small>College of Nursing</small></span>
  </a>
  <nav class="main-nav">
    <a class="active" href="#">Home</a>
    <a href="#">About</a>
    <a href="#">Academics</a>
    <a href="#">Policies &amp; Handbooks</a>
    <a href="#">Library</a>
    <a href="#">Contact Us</a>
    <a href="#">Donate</a>
  </nav>
</header>

<section class="hero">
  <div class="hero-photo" role="img" aria-label="Photo of nursing students seated in a classroom with blue chairs"></div>
  <div class="hero-shade"></div>
  <h1 class="serif">Corwin Ashby College Of Nursing</h1>
  <p>The Corwin Ashby College of Nursing (CACN) was founded in 1945 as a private, non-profit College, and is at the forefront of nursing education.</p>
  <a class="btn" href="#">Get Started</a>
  <svg class="hero-curve" viewBox="0 0 1200 130" preserveAspectRatio="none">
    <path d="M0 0 L0 130 L1200 130 L1200 20 C900 120 400 150 0 0 Z" fill="#fff"/>
    <path d="M90 48 C400 140 800 120 1200 20 C820 105 400 125 90 48 Z" fill="var(--navy)"/>
  </svg>
</section>

<section class="about-college">
  <svg class="arc" style="left:106px;top:840px" width="476" height="476"><path d="M10 230 A228 228 0 0 0 466 238" fill="none" stroke="var(--red)" stroke-width="7"/></svg>
  <div class="round-photo" style="left:112px;top:846px;background:linear-gradient(180deg,#8a6a4a 0%,#6b4f3a 40%,#23418c 60%,#1a2f6e 100%)" role="img" aria-label="Photo of a graduation ceremony with graduates in blue caps and gowns"></div>
  <h2 class="section-title" style="left:624px;top:834px">About the <span>College</span></h2>
  <div class="copy" style="left:624px;top:910px;width:475px">
    <p>Corwin Ashby College of Nursing will be nationally recognized for excellence in nursing education, and noted for its comprehensive, innovative academic programs that are responsive to the healthcare challenges of the future.Corwin Ashby College of Nursing is an independent single-purpose institution. Its mission is to provide a dynamic career-ladder approach to nursing education to improve professional practice and contribute to the health of communities.</p>
    <p>The College is located in Harlem, one of the most dynamic and safe communities in New York City. We are easily accessible from all boroughs, Long Island and the Tri-State Area via public transportation, commuter rail or car, although parking is limited. Classes are held during the day and evenings, Monday through Saturday.</p>
  </div>
  <a class="btn" href="#" style="left:624px;top:1258px">Get Started</a>
</section>

<section class="notice">
  <h2>NCNER Pre-accreditation<br>Public Posting Notice</h2>
  <p>he Associate Degree in Nursing Program at Corwin Ashby College of Nursing is seeking pre-accreditation status from the National Council for Nursing Education Review (NCNER), located at 1800 Linden Avenue, NW, Washington, DC, 20036; phone 202-555-0148. Holding pre-accreditation status does not guarantee that initial accreditation by NCNER will be received.</p>
  <a class="btn" href="#">Read More</a>
</section>

<section class="quick-cards">
  <article class="info-card" style="left:112px">
    <div class="icon"><svg width="30" height="30" viewBox="0 0 30 30" fill="none" stroke="var(--green)" stroke-width="1.6"><rect x="3" y="4" width="24" height="10" rx="2"/><path d="M14 12v10l-3-2 4 7h6l1-8-5-1"/></svg></div>
    <h3>Apply Now</h3>
    <ul><li>Generic BS Program (No LPN/-clinical background required)</li><li class="link">LPN to RN Program</li><li class="link">RN to BS Program</li><li class="link">Admissions Pathway</li></ul>
  </article>
  <article class="info-card" style="left:362px">
    <div class="icon"><svg width="30" height="30" viewBox="0 0 30 30" fill="none" stroke="var(--green)" stroke-width="1.6"><circle cx="12" cy="9" r="4"/><path d="M5 26l4-10h6l5 5M18 6l3-3M22 10h4"/></svg></div>
    <h3>Our Successes</h3>
    <ul><li>CACN is an independent single-purpose institution. Its mission is to provide a dynamic career-ladder approach to nursing education to improve ...</li></ul>
  </article>
  <article class="info-card featured" style="left:613px">
    <div class="icon"><svg width="30" height="30" viewBox="0 0 30 30" fill="none" stroke="#fff" stroke-width="1.6"><rect x="3" y="4" width="24" height="10" rx="2"/><path d="M14 12v10l-3-2 4 7h6l1-8-5-1"/></svg></div>
    <h3>Demographics</h3>
    <ul><li>Student Demographics</li><li>Graduating Students</li></ul>
  </article>
  <article class="info-card" style="left:863px">
    <div class="icon"><svg width="30" height="30" viewBox="0 0 30 30" fill="none" stroke="var(--green)" stroke-width="1.6"><rect x="3" y="4" width="24" height="10" rx="2"/><path d="M14 12v10l-3-2 4 7h6l1-8-5-1"/></svg></div>
    <h3>Information</h3>
    <ul><li class="link">Licensure Exam Pass Rate</li><li class="link">Consumer Information</li><li class="link">Contact Information</li><li class="link">AAS Course Information</li><li class="link">Fees Information ...</li></ul>
  </article>
</section>

<section class="about-library">
  <h2 class="section-title" style="left:112px;top:2312px">About the <span>Library</span></h2>
  <div class="copy" style="left:112px;top:2390px;width:475px">
    <p>The Nell Haverly Memorial Library, named after the College's former president, the late Dr. Eleanor (Nell) Haverly, is a major component of the Corwin Ashby educational experience. The Library houses a collection of books and periodicals selected to meet curriculum needs and student and faculty research interests. The library's collections are supplemented by memberships in resource-sharing consortia.</p>
    <p>These partnerships are integrated into the borrowing services provided through the interlibrary loan service and serve to expand the range of materials available to students. Audiovisual and computer assisted instructional resources supplement classroom instruction, enhance learning, and provide a means of independent study and research.</p>
  </div>
  <a class="btn" href="#" style="left:112px;top:2735px">Get Started</a>
  <svg class="arc" style="left:626px;top:2316px" width="476" height="476"><path d="M466 230 A228 228 0 0 1 10 238" fill="none" stroke="var(--red)" stroke-width="7" transform="rotate(-20 238 238)"/></svg>
  <div class="round-photo" style="left:630px;top:2321px;background:linear-gradient(135deg,#6a6258 0%,#3d3a3c 35%,#1d3a8a 65%,#25206b 100%)" role="img" aria-label="Photo of a smiling graduate in a blue cap and gown with a faculty member"></div>
</section>

<section class="news">
  <h2 class="section-title" style="left:0;width:1200px;text-align:center;top:2860px">News &amp; <span>Updates</span></h2>
  <article class="news-card" style="left:112px">
    <div class="thumb" style="background:linear-gradient(135deg,#6f7680,#9aa1a8 50%,#5c636c)" role="img" aria-label="College seal over a blurred campus photo"></div>
    <h3>Public Notice of Upcoming Accreditation Review Visit by the NAEB</h3>
    <p>Corwin Ashby College of Nursing wishes to announce that it will host a site visit for continuing accreditation ...</p>
    <a class="go" href="#"><svg width="16" height="16" viewBox="0 0 16 16"><path d="M2 8h11M9 3l5 5-5 5" stroke="#fff" stroke-width="2.4" fill="none"/></svg></a>
  </article>
  <article class="news-card" style="left:444px">
    <div class="thumb" style="background:linear-gradient(135deg,#6a3fb3,#8c62d0 55%,#b9a6e6)" role="img" aria-label="Open house flyer with program dates and a photo of a nurse"></div>
    <h3>Corwin Ashby College Of Nursing Open House</h3>
    <p>CACN January 2024 Open House Dates:<br>LPN to RN: January 17, 2024 at 11:00 am<br>(On Campus)</p>
    <a class="go" href="#"><svg width="16" height="16" viewBox="0 0 16 16"><path d="M2 8h11M9 3l5 5-5 5" stroke="#fff" stroke-width="2.4" fill="none"/></svg></a>
  </article>
  <article class="news-card" style="left:776px">
    <div class="thumb" style="background:linear-gradient(135deg,#cfcac4,#e9e6e1 50%,#a8a39d)" role="img" aria-label="Photo of a hand writing on paper with a pen"></div>
    <h3>Upcoming NEAT Testing</h3>
    <p>PRE-ADMISSION TESTING SCHEDULE<br>*Students must contact the admissions office (admission@corwinashby.edu) to schedule the NEAT exam. Walk-ins are not allowed.</p>
    <a class="go" href="#"><svg width="16" height="16" viewBox="0 0 16 16"><path d="M2 8h11M9 3l5 5-5 5" stroke="#fff" stroke-width="2.4" fill="none"/></svg></a>
  </article>
  <a class="btn" href="#" style="left:526px;top:3398px">View All</a>
</section>

<footer class="site-footer">
  <svg class="abs" style="left:0;top:0" width="1200" height="603" viewBox="0 0 1200 603" preserveAspectRatio="none">
    <path d="M0 90 C400 -20 800 -20 1200 90 L1200 603 L0 603 Z" fill="var(--dark)"/>
    <path d="M110 60 C450 -25 780 -20 1090 70 C780 0 450 0 110 60 Z" fill="var(--navy)"/>
  </svg>
  <div class="footer-seal" role="img" aria-label="Corwin Ashby College of Nursing seal"></div>

  <div class="fcol" style="left:114px">
    <h4>About Us</h4>
    <p style="font-size:14.5px;line-height:25px;width:250px">Corwin Ashby College of Nursing has been educating nurses for over seventy years.</p>
    <div class="social"><span></span><span></span><span></span><span></span></div>
  </div>

  <div class="fcol" style="left:422px;top:278px">
    <h4>Contact Us</h4>
    <div class="contact-row"><svg width="20" height="20" viewBox="0 0 24 24" fill="none" stroke="#fff" stroke-width="1.6"><path d="M5 3h4l2 5-3 2a11 11 0 0 0 6 6l2-3 5 2v4a2 2 0 0 1-2 2A17 17 0 0 1 3 5a2 2 0 0 1 2-2z"/></svg><span>(212) 555-0172/0178</span></div>
    <div class="contact-row"><svg width="20" height="20" viewBox="0 0 24 24" fill="none" stroke="#fff" stroke-width="1.6"><rect x="3" y="5" width="18" height="14" rx="1"/><path d="M3 6l9 7 9-7"/></svg><span>registrar@corwinashby.edu</span></div>
    <div class="contact-row"><svg width="20" height="20" viewBox="0 0 24 24" fill="none" stroke="#fff" stroke-width="1.6"><path d="M12 22s7-7 7-12a7 7 0 0 0-14 0c0 5 7 12 7 12z"/><circle cx="12" cy="10" r="2.5"/></svg><span>48 E 131st St, New York, NY<br>10037, United States</span></div>
  </div>

  <div class="fcol" style="left:720px;top:276px">
    <h4>Quick Link</h4>
    <ul><li>Office Suite</li><li>Course Portal</li><li>Student Portal</li><li>Email</li><li>Exam Testing</li></ul>
  </div>

  <div class="fcol" style="left:922px;top:276px">
    <h4>Other Links</h4>
    <ul><li>Proctor Hub</li><li>Textbook Connect</li><li>Payroll (employees Only)</li><li>Pay Portal (staff Only)</li><li>Records System</li></ul>
  </div>

  <p class="copyright">© 2024 by Corwin Ashby College Of Nursing.</p>
</footer>

</body>
</html>
```